BOLD & MINIMALIST DESIGN NEEDED

We want a very bold but minimalistic business card design that is impactful and utilizes both sides of the business card. Our current logo is included for your use.

We want bold fonts and good use of negative space. We don't want the logo to overpower the design.

Target Market(s)

Professionals who are building new commercial buildings.

Industry/Entity Type

Construction

Contact Information for Business Card

Name, Title, email, office phone, cell phone, website

Font styles to use
Serif
Sans Serif

Requirements
Must have
• Bold design!

```html
<!DOCTYPE html>
<html lang="en">
<head>
<meta charset="utf-8">
<title>Ridgeline Build – Stationery Set</title>
<link href="https://fonts.googleapis.com/css2?family=Source+Sans+3:wght@300;400;700&family=Crimson+Text:wght@400&display=swap" rel="stylesheet">
<style>
:root{
  --board:#1f2021;
  --paper:#ffffff;
  --ink:#0c0c0c;
  --green:#7cc242;
  --label:#f2f2f2;
  --text:#3a3a3a;
  --rule:#b8b8b8;
}
*{margin:0;padding:0;box-sizing:border-box}
html,body{width:953px;height:1200px;overflow:hidden}
body{background:var(--board);position:relative;font-family:"Crimson Text",Georgia,serif;color:var(--text)}
.piece-title{position:absolute;font-family:"Source Sans 3",Arial,sans-serif;font-weight:300;font-size:17px;color:var(--label);letter-spacing:.2px}
.sheet{position:absolute;background:var(--paper);overflow:hidden}
.sheet .band{position:absolute;inset:0;width:100%;height:100%}
.wordmark{position:absolute;display:flex;align-items:center;gap:5px;font-family:"Source Sans 3",Arial,sans-serif;font-weight:700;color:var(--ink);letter-spacing:.5px;white-space:nowrap}
.wordmark .mark{display:block;background:var(--green)}
.contacts{position:absolute;list-style:none;font-size:7px;line-height:10.6px}
.contacts li{display:flex;align-items:center;gap:3px}
.icon{width:6px;height:6px;flex:none}
.address{position:absolute;display:flex;align-items:center;gap:3px;font-size:7px;color:var(--paper)}
.note-lines{position:absolute;left:13px;right:13px;top:73px}
.note-lines span{display:block;height:16.5px;border-top:.6px solid var(--rule)}
.compliments{position:absolute;font-family:"Source Sans 3",Arial,sans-serif;font-weight:700;font-size:12px;color:var(--paper)}
.card-name{position:absolute;font-size:9px;color:var(--green)}
.card-role{position:absolute;font-size:6.5px;color:var(--ink)}
.card-rule{position:absolute;height:0;border-top:.6px solid #666}
.card-web{position:absolute;font-size:7px;color:var(--green);letter-spacing:1.5px}
</style>
</head>
<body>
<svg width="0" height="0" style="position:absolute">
  <defs>
    <symbol id="i-phone" viewBox="0 0 10 10"><path d="M2 1l2 2-1 1.3c.6 1.2 1.5 2.1 2.7 2.7L7 6l2 2-1.3 1.3C4.5 9 1 5.5.7 2.3z" fill="#7cc242"/></symbol>
    <symbol id="i-mobile" viewBox="0 0 10 10"><rect x="2.5" y=".5" width="5" height="9" rx="1" fill="none" stroke="#7cc242" stroke-width="1"/></symbol>
    <symbol id="i-mail" viewBox="0 0 10 10"><rect x=".5" y="2" width="9" height="6" fill="#7cc242"/><path d="M.5 2l4.5 3.5L9.5 2" fill="none" stroke="#fff" stroke-width=".8"/></symbol>
    <symbol id="i-web" viewBox="0 0 10 10"><circle cx="5" cy="5" r="4.3" fill="none" stroke="#7cc242" stroke-width="1"/><path d="M.7 5h8.6M5 .7c-2.4 2.6-2.4 6 0 8.6M5 .7c2.4 2.6 2.4 6 0 8.6" fill="none" stroke="#7cc242" stroke-width=".7"/></symbol>
    <symbol id="i-pin" viewBox="0 0 10 10"><path d="M5 .5a3.2 3.2 0 0 1 3.2 3.2C8.2 6 5 9.5 5 9.5S1.8 6 1.8 3.7A3.2 3.2 0 0 1 5 .5z" fill="#7cc242"/><circle cx="5" cy="3.7" r="1.2" fill="#0c0c0c"/></symbol>
  </defs>
</svg>

<!-- Business cards -->
<h2 class="piece-title" style="left:77px;top:57px">Business card_1</h2>

<section class="sheet business-card card-front" style="left:122px;top:124px;width:300px;height:171px">
  <svg class="band" viewBox="0 0 300 171" preserveAspectRatio="none"><path d="M0 132H170C210 124 238 100 300 97V171H0Z" fill="#0c0c0c"/></svg>
  <div class="wordmark" style="left:40px;top:88px;font-size:17px"><span class="mark" style="width:10px;height:10px"></span>RIDGELINE BUILD</div>
  <div class="card-web" style="left:40px;top:150px">www.ridgeline-build.com</div>
</section>

<section class="sheet business-card card-back" style="left:122px;top:305px;width:300px;height:171px">
  <svg class="band" viewBox="0 0 300 171" preserveAspectRatio="none"><path d="M0 150H180C218 142 245 118 300 115V171H0Z" fill="#0c0c0c"/></svg>
  <div class="wordmark" style="right:14px;top:14px;font-size:11px"><span class="mark" style="width:7px;height:7px"></span>RIDGELINE BUILD</div>
  <div class="card-name" style="left:16px;top:64px">Dana Whitfield</div>
  <div class="card-role" style="left:16px;top:77px">Founder</div>
  <div class="card-rule" style="left:46px;right:16px;top:84px"></div>
  <ul class="contacts" style="left:16px;top:94px">
    <li><svg class="icon"><use href="#i-mobile"/></svg>555-019-4410</li>
    <li><svg class="icon"><use href="#i-phone"/></svg>555-014-2200</li>
    <li><svg class="icon"><use href="#i-mail"/></svg>info@ridgeline-build.com</li>
    <li><svg class="icon"><use href="#i-web"/></svg>www.ridgeline-build.com</li>
  </ul>
  <div class="address" style="left:16px;top:156px"><svg class="icon"><use href="#i-pin"/></svg>1420 Quarry Ln. Ashford, GA 30500</div>
</section>

<!-- Letterhead -->
<h2 class="piece-title" style="left:499px;top:57px">Letterhead_1</h2>
<section class="sheet letterhead" style="left:499px;top:97px;width:377px;height:488px">
  <svg class="band" viewBox="0 0 377 488" preserveAspectRatio="none"><path d="M0 460H161C220 446 300 440 377 452V488H0Z" fill="#0c0c0c"/></svg>
  <div class="wordmark" style="right:13px;top:42px;font-size:14px"><span class="mark" style="width:8px;height:8px"></span>RIDGELINE BUILD</div>
  <ul class="contacts" style="left:14px;top:427px">
    <li><svg class="icon"><use href="#i-phone"/></svg>555-014-2200</li>
    <li><svg class="icon"><use href="#i-mail"/></svg>info@ridgeline-build.com</li>
    <li><svg class="icon"><use href="#i-web"/></svg>www.ridgeline-build.com</li>
  </ul>
  <div class="address" style="left:14px;top:465px"><svg class="icon"><use href="#i-pin"/></svg>1420 Quarry Ln. Ashford, GA 30500</div>
</section>

<!-- Note pad -->
<h2 class="piece-title" style="left:77px;top:580px">Note Pads_1</h2>
<section class="sheet note-pad" style="left:77px;top:618px;width:360px;height:254px">
  <svg class="band" viewBox="0 0 360 254" preserveAspectRatio="none"><path d="M0 226H157C220 212 300 206 360 220V254H0Z" fill="#0c0c0c"/></svg>
  <div class="wordmark" style="right:14px;top:42px;font-size:12px"><span class="mark" style="width:7px;height:7px"></span>RIDGELINE BUILD</div>
  <div class="note-lines"><span></span><span></span><span></span><span></span><span></span><span></span><span></span><span></span></div>
  <ul class="contacts" style="left:16px;top:195px">
    <li><svg class="icon"><use href="#i-phone"/></svg>555-014-2200</li>
    <li><svg class="icon"><use href="#i-mail"/></svg>info@ridgeline-build.com</li>
    <li><svg class="icon"><use href="#i-web"/></svg>www.ridgeline-build.com</li>
  </ul>
  <div class="address" style="left:16px;top:230px"><svg class="icon"><use href="#i-pin"/></svg>1420 Quarry Ln. Ashford, GA 30500</div>
</section>

<!-- Compliment slip -->
<h2 class="piece-title" style="left:492px;top:651px">Comp Slips_1</h2>
<section class="sheet comp-slip" style="left:492px;top:691px;width:384px;height:181px">
  <svg class="band" viewBox="0 0 384 181" preserveAspectRatio="none"><path d="M0 153H213C260 143 330 138 384 148V181H0Z" fill="#0c0c0c"/></svg>
  <div class="wordmark" style="left:13px;top:40px;font-size:13px"><span class="mark" style="width:8px;height:8px"></span>RIDGELINE BUILD</div>
  <ul class="contacts" style="left:13px;top:121px">
    <li><svg class="icon"><use href="#i-phone"/></svg>555-014-2200</li>
    <li><svg class="icon"><use href="#i-mail"/></svg>info@ridgeline-build.com</li>
    <li><svg class="icon"><use href="#i-web"/></svg>www.ridgeline-build.com</li>
  </ul>
  <div class="address" style="left:13px;top:157px"><svg class="icon"><use href="#i-pin"/></svg>1420 Quarry Ln. Ashford, GA 30500</div>
  <div class="compliments" style="left:252px;top:151px">With Compliments</div>
</section>

<!-- Envelope front -->
<h2 class="piece-title" style="left:77px;top:911px">ENV Front_1</h2>
<section class="sheet envelope-front" style="left:77px;top:951px;width:388px;height:168px">
  <svg class="band" viewBox="0 0 388 168" preserveAspectRatio="none"><path d="M0 144H257C300 134 350 132 388 138V168H0Z" fill="#0c0c0c"/></svg>
  <div class="wordmark" style="left:13px;top:44px;font-size:13px"><span class="mark" style="width:8px;height:8px"></span>RIDGELINE BUILD</div>
  <div class="address" style="left:13px;top:150px"><svg class="icon"><use href="#i-pin"/></svg>1420 Quarry Ln. Ashford, GA 30500</div>
</section>

<!-- Envelope back -->
<h2 class="piece-title" style="left:499px;top:911px">ENV Back_1</h2>
<section class="sheet envelope-back" style="left:499px;top:951px;width:386px;height:169px">
  <svg class="band" viewBox="0 0 386 169" preserveAspectRatio="none"><path d="M2 0C10 20 16 34 30 37L162 57C180 63 206 63 224 57L356 37C370 34 376 20 384 0" fill="none" stroke="#0c0c0c" stroke-width="4"/><path d="M168 58C182 50 204 50 218 58C204 63 182 63 168 58Z" fill="#0c0c0c"/></svg>
  <div class="wordmark" style="left:163px;top:35px;font-size:9px"><span class="mark" style="width:5px;height:5px"></span>RIDGELINE</div>
</section>
</body>
</html>
```